Tovin Brightway Website Design

About The Client:
Tovin Brightway is a sugar-free foods chain store providing services to Diabetics. They focus on the China domestic market. They describe themselves as being the 3rd space for Diabetics, the space between hospital and the home that help improve the quality of life for people wit Diabetes (see attached infographics).

They regularly hold education and advice events throughout the China. Tovin Brightway distribute a wide product range of food that is suitable for diabetic people. Tovin Brightway operate as a Franchise, providing business development services and Industry knowledge. They are actively seeking business partnerships at present.

The Brief:
Design a Home page and secondary information page(PSD only no code) that communicates our company services and company philosophy(3rd Space).
The final design should communicate 'Health, Social Responsibility and Professionalism'.
Colour scheme should orientate around Blue and White, see attached logo.

Websites we like:

http://lumo.vextaran.com/home/

https://www.pondrelix.com/

http://gate.zt.com/

Hello all, the client has advised us that he want to display the professional advice service available for diabetic people more so than a food distributor. The client is also hoping to use his website as a marketing platform to attract affiliates and build partnerships as part of Tovin Brightway's business expansion strategy.

So can you make the page more corporate, reliable and professional. Use images of experts/doctors interacting with patients and also training/knowledge transfer images.

Thanks

Hello all, could you include stock images of both Chinese and Caucasians

Yeaahhh, Infographics and photos have been uploaded. Feel free to use them in your designs and also as references.

Target Market(s)

The target market is Chinese B2B in the Diabetics industry and Entrepreneurs looking to cooperate with Tovin Brightway.

Industry/Entity Type

Education

Requirements
Must have
• menu navigation with 7-8 sections,
a full screen background image,
Social Media icons,
Logo in top left,
Site search.
Nice to have
• The website must be clear and easy to use, less complicated.

See attached files of some Tovin Brightway infographics. Feel free to include elements of these into the design.
Should not have
• Should not use stock images of people from any other country, the client wants stock images of Chinese people only. Avoid photos showing obesity.

```html
<!DOCTYPE html>
<html lang="en">
<head>
<meta charset="utf-8">
<title>Tovin Brightway — Home</title>
<link href="https://fonts.googleapis.com/css2?family=Open+Sans:wght@400;600;700&display=swap" rel="stylesheet">
<style>
:root{
  --red:#e2202a;
  --red-dark:#c3141d;
  --blue:#1b77c9;
  --ink:#333;
  --muted:#7a7a7a;
  --line:#e3e3e3;
  --topbar:#2a2a2a;
  --footer:#2e2e2e;
  --footer-deep:#222;
  --white:#fff;
}
*{box-sizing:border-box;margin:0;padding:0}
html,body{width:705px;height:1200px;overflow:hidden;background:var(--white)}
body{font-family:"Open Sans",Arial,sans-serif;color:var(--ink);font-size:7px;line-height:1.45}
.page{width:705px;height:1200px;position:relative}

/* top bar */
.topbar{height:20px;background:var(--topbar);color:#ddd;display:flex;align-items:center;justify-content:space-between;padding:0 30px;font-size:6.5px;font-weight:600}
.topbar-links span{margin-right:4px}
.topbar-links .sep{color:#777}
.topbar-right{display:flex;align-items:center;gap:10px}
.cart{display:flex;align-items:center;gap:4px}
.lang{width:24px;height:10px;background:#fff;border-radius:1px;display:flex;align-items:center;justify-content:center;color:#333;font-size:5px}

/* header */
.header{height:86px;display:flex;align-items:center;justify-content:space-between;padding:0 30px}
.brand{display:flex;align-items:center;gap:7px}
.brand-mark{width:26px;height:26px;border-radius:50%;background:var(--blue)}
.brand-name{font-size:13px;font-weight:700;color:var(--blue);line-height:1.1;width:80px}
.search{width:118px;height:18px;border:1px solid #ccc;display:flex;align-items:center;justify-content:space-between;padding:0 5px;color:#999;font-size:6.5px}

/* nav */
.nav{height:20px;background:var(--red);display:flex;align-items:center;padding:0 30px}
.nav a{color:#fff;text-decoration:none;font-size:7px;font-weight:600;padding:0 11px;height:20px;line-height:20px}
.nav a.active{background:var(--red-dark)}

/* hero */
.hero{position:relative;height:305px}
.hero-photo{position:absolute;inset:0;background:linear-gradient(100deg,#5d5550 0%,#a8917f 28%,#e2d3c3 52%,#c9ad95 72%,#4f4640 100%)}
.hero-caption{position:absolute;left:30px;bottom:36px;width:225px;background:rgba(0,0,0,.6);color:#fff;padding:8px 10px}
.hero-caption h2{font-size:11px;font-weight:700;margin-bottom:3px}
.hero-caption p{font-size:6.5px;color:#ddd}
.hero-dots{position:absolute;right:32px;bottom:10px;display:flex;gap:4px}
.hero-dots i{width:6px;height:6px;border-radius:50%;background:rgba(255,255,255,.6)}
.hero-dots i.on{background:#fff}

/* welcome + news */
.intro{display:flex;gap:22px;padding:20px 30px 0;height:234px}
.welcome{flex:1}
.section-title{font-size:11px;font-weight:700;color:#222;padding-bottom:6px;border-bottom:1px solid var(--line);margin-bottom:10px}
.welcome-body{display:flex;gap:10px}
.welcome-photo{width:92px;height:130px;flex:none;background:linear-gradient(160deg,#3d3430,#a88470 45%,#dcc6b2)}
.welcome-lead{color:var(--blue);font-size:7.5px;font-weight:600;margin-bottom:5px;line-height:1.35}
.welcome-text p{margin-bottom:5px;color:var(--muted);font-size:6.5px}
.news{width:190px}
.news-item{display:flex;gap:7px;margin-bottom:12px}
.news-thumb{width:38px;height:32px;flex:none;background:linear-gradient(135deg,#5f6f82,#c9d3de)}
.news-item h4{font-size:6.5px;font-weight:700;color:#222}
.news-item p{color:var(--muted);font-size:6px}

/* services */
.services{padding:0 30px;height:196px}
.service-grid{display:flex;gap:18px}
.service{flex:1}
.service-photo{height:92px;margin-bottom:6px}
.service h3{color:var(--blue);font-size:8px;font-weight:700;margin-bottom:2px}
.service p{color:var(--muted);font-size:6.5px}

/* products */
.products{padding:0 30px;height:225px}
.products-head{display:flex;justify-content:space-between;align-items:flex-start}
.products-head .section-title{flex:1}
.arrows{display:flex;gap:3px;margin-left:6px}
.arrows span{width:12px;height:12px;border-radius:50%;background:#999;display:flex;align-items:center;justify-content:center}
.product-grid{display:flex;gap:18px}
.product{flex:1}
.product-box{height:124px;border:1px solid #d8d8d8;display:flex;align-items:center;justify-content:center;margin-bottom:7px}
.product-shot{width:62%;height:70%}
.product p{font-size:6.5px;color:#444;text-align:center;line-height:1.35}

/* footer */
.footer{position:absolute;left:0;right:0;top:1110px;height:90px;background:var(--footer);color:#bbb}
.footer-cols{display:flex;padding:7px 30px 0;gap:14px;height:72px}
.footer-col h5{color:#fff;font-size:6.5px;font-weight:700;margin-bottom:3px}
.footer-col li{list-style:none;font-size:5.5px;line-height:1.55}
.col-sm{width:78px}
.newsletter{width:100px}
.field{height:11px;background:#fff;margin-bottom:3px;color:#999;font-size:5.5px;padding:0 4px;line-height:11px}
.btn{display:inline-block;background:var(--red);color:#fff;font-size:5.5px;font-weight:700;padding:1px 7px}
.social li{display:flex;align-items:center;gap:5px;margin-bottom:3px}
.social i{width:9px;height:9px;border-radius:50%;background:var(--blue);display:block}
.social li:nth-child(2) i{background:var(--red)}
.footer-bottom{height:18px;background:var(--footer-deep);display:flex;align-items:center;justify-content:space-between;padding:0 30px;font-size:5.5px}
.payments{display:flex;gap:3px}
.payments span{background:#fff;color:#333;font-size:5px;font-weight:600;padding:1px 4px;border-radius:1px}
</style>
</head>
<body>
<div class="page">

  <div class="topbar">
    <div class="topbar-links">
      <span>MY ACCOUNT</span><span class="sep">|</span>
      <span>SIGN IN</span><span class="sep">|</span>
      <span>CHECK OUT</span><span class="sep">|</span>
      <span>CONTACT US</span>
    </div>
    <div class="topbar-right">
      <div class="cart">
        <svg width="10" height="9" viewBox="0 0 10 9"><path d="M0 1h2l1.2 5h5L9.5 2.5H3" fill="none" stroke="#ddd" stroke-width="1"/><circle cx="4" cy="8" r=".8" fill="#ddd"/><circle cx="7.5" cy="8" r=".8" fill="#ddd"/></svg>
        <span>Cart (0) Items</span>
      </div>
      <div class="lang">EN ▾</div>
    </div>
  </div>

  <header class="header">
    <div class="brand">
      <span class="brand-mark"></span>
      <span class="brand-name">Tovin Brightway</span>
    </div>
    <div class="search">
      <span>Search</span>
      <svg width="8" height="8" viewBox="0 0 8 8"><circle cx="3.2" cy="3.2" r="2.4" fill="none" stroke="#888" stroke-width="1"/><path d="M5 5l2.5 2.5" stroke="#888" stroke-width="1"/></svg>
    </div>
  </header>

  <nav class="nav">
    <a class="active">HOME</a><a>ABOUT US</a><a>PRODUCTS</a><a>SERVICES</a><a>BEST SELLERS</a><a>BLOGS</a><a>TESTIMONIALS</a><a>CONTACT</a>
  </nav>

  <section class="hero">
    <div class="hero-photo" role="img" aria-label="Photo of a smiling group of young Chinese friends"></div>
    <div class="hero-caption">
      <h2>Amet dolor sit tation ullamcorper</h2>
      <p>Dolor sit amet magna. Nullam sollicitudin dolor, ipsum sed hendrerit aliquam, nisl vitae pellentesque odio.</p>
    </div>
    <div class="hero-dots"><i></i><i></i><i class="on"></i><i></i></div>
  </section>

  <section class="intro">
    <div class="welcome">
      <h2 class="section-title">Welcome to Tovin Brightway</h2>
      <div class="welcome-body">
        <div class="welcome-photo" role="img" aria-label="Photo of a smiling woman with a child"></div>
        <div class="welcome-text">
          <p class="welcome-lead">Sugar Free Ice Products Manufacturer &amp; Nationwide Distributor of Sugar Free Products</p>
          <p>Incididunt ut labore et dolore magna aliqua. Ut enim ad minim veniam, quis nostrud exercitation ullamco laboris nisi ut aliquip ex ea commodo consequat. Duis aute irure dolor in reprehenderit in voluptate velit esse cillum dolore.</p>
          <p>Excepteur sint occaecat cupidatat non proident, sunt in culpa qui officia deserunt mollit anim id est laborum sed ut perspiciatis unde omnis iste natus error sit voluptatem.</p>
          <p>Quis nostrud exercitation ullamco laboris nisi ut aliquip. Ut enim ad minim veniam, quis nostrud exercitation laboris. Cras tincidunt libero a rhoncus dignissim, sed porttitor imperdiet leo.</p>
        </div>
      </div>
    </div>
    <aside class="news">
      <h2 class="section-title">Latest News</h2>
      <div class="news-item">
        <div class="news-thumb" role="img" aria-label="News photo"></div>
        <div><h4>During November 2013</h4><p>Our Principal Fellows spoke on the local education about diet.</p></div>
      </div>
      <div class="news-item">
        <div class="news-thumb" role="img" aria-label="News photo"></div>
        <div><h4>During November 2013</h4><p>It is one of our successful in our diet program discusses again.</p></div>
      </div>
      <div class="news-item">
        <div class="news-thumb" role="img" aria-label="News photo"></div>
        <div><h4>During November 2013</h4><p>Nam libero tempore cum soluta nobis est eligendi.</p></div>
      </div>
    </aside>
  </section>

  <section class="services">
    <h2 class="section-title">Our Services</h2>
    <div class="service-grid">
      <div class="service">
        <div class="service-photo" role="img" aria-label="Photo of a doctor advising a patient" style="background:linear-gradient(135deg,#b9c6d2,#f1ece6 55%,#c9b3a2)"></div>
        <h3>Doctor's Advice</h3>
        <p>Nunc venenatis lacinia lacus quis vulputate. Sed porttitor imperdiet leo sed urna molestie.</p>
      </div>
      <div class="service">
        <div class="service-photo" role="img" aria-label="Photo of shelves of sugar free food products" style="background:linear-gradient(135deg,#c79a5b,#b4533f 50%,#6d8fb3)"></div>
        <h3>Best Sugar Free Products</h3>
        <p>Nunc venenatis lacinia lacus quis vulputate. Sed porttitor imperdiet leo sed urna molestie.</p>
      </div>
      <div class="service">
        <div class="service-photo" role="img" aria-label="Photo of medication tablets" style="background:linear-gradient(135deg,#eef2f6,#c9d8e6 45%,#d56c5a)"></div>
        <h3>Medications</h3>
        <p>Nunc venenatis lacinia lacus quis vulputate. Sed porttitor imperdiet leo sed urna molestie.</p>
      </div>
    </div>
  </section>

  <section class="products">
    <div class="products-head">
      <h2 class="section-title">Our Products</h2>
      <div class="arrows">
        <span><svg width="5" height="6" viewBox="0 0 5 6"><path d="M4 0L1 3l3 3" fill="none" stroke="#fff" stroke-width="1.2"/></svg></span>
        <span><svg width="5" height="6" viewBox="0 0 5 6"><path d="M1 0l3 3-3 3" fill="none" stroke="#fff" stroke-width="1.2"/></svg></span>
      </div>
    </div>
    <div class="product-grid">
      <div class="product">
        <div class="product-box"><div class="product-shot" role="img" aria-label="Product photo of a sugar free milk powder tin" style="background:linear-gradient(180deg,#6aa85c,#eef2e0)"></div></div>
        <p>Nullam at dolor sit amet an<br>im bibendum accumsan</p>
      </div>
      <div class="product">
        <div class="product-box"><div class="product-shot" role="img" aria-label="Product photo of sugar free snack packs" style="background:linear-gradient(180deg,#eed46a,#d0584a)"></div></div>
        <p>Nullam at dolor sit amet an<br>im bibendum accumsan</p>
      </div>
      <div class="product">
        <div class="product-box"><div class="product-shot" role="img" aria-label="Product photo of a sugar free biscuit box" style="background:linear-gradient(180deg,#4a83c2,#f0b25a)"></div></div>
        <p>Nullam at dolor sit amet an<br>im bibendum accumsan</p>
      </div>
      <div class="product">
        <div class="product-box"><div class="product-shot" role="img" aria-label="Product photo of sugar free candy bags" style="background:linear-gradient(180deg,#de5e55,#5a84c0)"></div></div>
        <p>Nullam at dolor sit amet an<br>im bibendum accumsan</p>
      </div>
    </div>
  </section>

  <footer class="footer">
    <div class="footer-cols">
      <div class="footer-col col-sm">
        <h5>COMPANY</h5>
        <ul><li>Blue Mind</li><li>Keep it Green</li><li>Follow of Care</li><li>Blizzard</li><li>Best Salt</li></ul>
      </div>
      <div class="footer-col col-sm">
        <h5>MORE</h5>
        <ul><li>Herbal Shreds</li><li>Key Shreds</li><li>Fruity Shreds</li><li>Regulations</li><li>Ergonomic Shreds</li><li>Beef Shreds</li></ul>
      </div>
      <div class="footer-col" style="width:110px">
        <h5>CONTACT US</h5>
        <ul><li>Tovin Brightway Inc.</li><li>12 Lantern Rd, Riverton</li><li>Tel: 555-0142</li><li>Phone: 555-0178</li></ul>
      </div>
      <div class="footer-col newsletter">
        <h5>Newsletter Signup</h5>
        <div class="field">Name</div>
        <div class="field">Email</div>
        <span class="btn">SUBMIT</span>
      </div>
      <div class="footer-col">
        <h5>Connect with us</h5>
        <ul class="social"><li><i></i>Friendwall</li><li><i></i>Pinboardly</li><li><i></i>Chirpline</li></ul>
      </div>
    </div>
    <div class="footer-bottom">
      <span>Copyright 2013. All Rights Reserved.</span>
      <div class="payments"><span>Cardora</span><span>Paynex</span><span>Tallymark</span></div>
    </div>
  </footer>

</div>
</body>
</html>
```